Now Leasing Banner

Looking for a banner that says the following information approx 4' x 30'

Now Leasing Maplebrook Terrace 925-318-6042

Target Market(s)

Drive by traffic

Industry/Entity Type

Residential property management

Requirements
Must have
• Clear and readable from a distance

```html
<!DOCTYPE html>
<html lang="en">
<head>
<meta charset="utf-8">
<title>Now Leasing Banner – Maplebrook Terrace</title>
<link rel="stylesheet" href="https://fonts.googleapis.com/css2?family=Antonio:wght@700&family=Tinos:wght@700&display=swap">
<style>
  :root {
    --brand-red: #a80000;
    --deep-red: #6e0000;
    --accent-yellow: #ffe000;
    --soft-gold: #f3e690;
    --paper: #ffffff;
    --frame-grey: #c4c4c4;
  }
  html, body {
    margin: 0;
    padding: 0;
    width: 1200px;
    height: 325px;
    overflow: hidden;
    background: var(--paper);
  }
  .banner {
    display: block;
    width: 1200px;
    height: 325px;
  }
  .banner-frame {
    fill: var(--paper);
    stroke: var(--frame-grey);
    stroke-width: 1.2;
    filter: drop-shadow(1px 2px 1.5px rgba(0,0,0,0.18));
  }
  .divider-glow { fill: var(--soft-gold); }
  .leasing-panel { fill: var(--brand-red); }
  .property-name {
    font-family: "Antonio", "Oswald", sans-serif;
    font-weight: 700;
    fill: var(--brand-red);
  }
  .headline,
  .phone-number {
    font-family: "Tinos", "Times New Roman", serif;
    font-weight: 700;
    stroke: var(--deep-red);
    stroke-width: 1;
    paint-order: stroke fill;
    filter: drop-shadow(1px 1.5px 0 rgba(60,0,0,0.7));
  }
  .headline { fill: var(--accent-yellow); }
  .phone-number { fill: var(--paper); }
</style>
</head>
<body>
<svg class="banner" viewBox="0 0 1200 325" xmlns="http://www.w3.org/2000/svg" aria-label="Now Leasing banner for Maplebrook Terrace">
  <rect class="banner-frame" x="41" y="87" width="1125" height="151"/>

  <path class="divider-glow" d="M588,87 Q680,162.5 588,238 L1166,238 L1166,87 Z"/>
  <path class="leasing-panel" d="M602,87 Q640,162.5 602,238 L1166,238 L1166,87 Z"/>

  <text class="property-name" x="69" y="210" font-size="126" textLength="512" lengthAdjust="spacingAndGlyphs">MAPLEBROOK TERRACE</text>

  <text class="headline" x="674" y="155" font-size="66" textLength="450" lengthAdjust="spacingAndGlyphs">NOW LEASING</text>
  <text class="phone-number" x="675" y="222" font-size="82" textLength="454" lengthAdjust="spacingAndGlyphs">925.318.6042</text>
</svg>
</body>
</html>
```